Sports / Entertainment Media Co needs a biz card design

We are a media co / luxury lifestyle brand that targets professional athletes, entertainers and high net-worth fans. We are currently preparing for a relaunch and in need for new biz cards. I envision a black on black card with a pop of color on opposite side. Color Palette black, white, red etc. I want this card to exude sexiness and power. Very high stylized, hip and cool. I have attached the logo - I would like to see it all in black, but also open to other ideas. I will also upload a current card with all information needed on this new card. Furthermore I will add some samples of other cards I love. Thanks!!!
Updates

I provided suggestions, however I am open to all ideas!!   Be as creative as you can.  Think cutting-edge, sexy and powerful.  Take a look at the cards I uploaded to get a sense for what I like.  Thanks!!!

Industry/Entity Type

Entertainment

```html
<!DOCTYPE html>
<html lang="en">
<head>
<meta charset="UTF-8">
<title>Pivot – Business Card</title>
<link rel="stylesheet" href="https://fonts.googleapis.com/css2?family=Exo+2:wght@400;500;800&display=swap">
<style>
  :root {
    --backdrop: #6b6b6b;
    --card: #141414;
    --card-shade: #050505;
    --frame: #3c3c3c;
    --ink-dark: #2a2a2a;
    --text-light: #d6d6d6;
    --name-light: #f2f2f2;
    --accent-red: #e0161e;
  }
  * { margin: 0; padding: 0; box-sizing: border-box; }
  html, body {
    width: 1200px; height: 675px; overflow: hidden;
    background: var(--backdrop);
    font-family: "Exo 2", sans-serif;
  }
  .stage {
    position: relative; width: 1200px; height: 675px;
    display: flex; align-items: center; justify-content: center; gap: 40px;
  }
  .card {
    position: relative; width: 520px; height: 300px;
    border-radius: 32px;
    background: linear-gradient(135deg, var(--card) 40%, var(--card-shade) 100%);
    overflow: hidden;
  }
  .card-back { background: var(--card-shade); }

  .speech-frame { position: absolute; inset: 0; }

  .brand {
    position: absolute; left: 78px; top: 58px;
    display: flex; align-items: center; gap: 12px;
  }
  .brand-name {
    font-weight: 800; font-size: 54px; letter-spacing: 1px;
    color: var(--name-light); line-height: 1;
  }
  .brand-dot {
    width: 14px; height: 14px; border-radius: 50%;
    background: var(--accent-red);
  }

  .person { position: absolute; right: 48px; top: 128px; text-align: right; }
  .person-name {
    font-size: 24px; font-weight: 500; letter-spacing: 2px;
    color: var(--name-light); text-transform: uppercase; line-height: 1.1;
  }
  .person-role {
    font-size: 12px; font-weight: 500; letter-spacing: 1px;
    color: var(--accent-red); text-transform: uppercase;
  }

  .contact-line {
    position: absolute; display: flex; align-items: center; gap: 8px;
    font-size: 14px; letter-spacing: 1px; color: var(--text-light);
    white-space: nowrap;
  }
  .contact-line svg { width: 14px; height: 14px; flex: none; }
  .phone { left: 44px; top: 206px; }
  .mobile { left: 44px; top: 230px; }
  .email { left: 276px; top: 222px; }
  .web { left: 276px; top: 248px; }
  .address { left: 44px; top: 266px; }

  .divider {
    position: absolute; left: 258px; top: 228px; height: 40px;
    border-left: 3px dotted var(--accent-red);
  }

  .back-brand {
    position: absolute; inset: 0;
    display: flex; align-items: center; justify-content: center; gap: 22px;
  }
  .back-brand .brand-name { font-size: 110px; letter-spacing: 2px; }
  .back-brand .brand-dot { width: 26px; height: 26px; }
</style>
</head>
<body>
<main class="stage">
  <section class="card card-front" aria-label="Business card front">
    <svg class="speech-frame" viewBox="0 0 520 300" aria-hidden="true">
      <path d="M70,30 H460 A30,30 0 0 1 490,60 V160 A30,30 0 0 1 460,190 H272 L236,222 L238,190 H70 A30,30 0 0 1 40,160 V60 A30,30 0 0 1 70,30 Z"
            fill="#0c0c0c" stroke="#3c3c3c" stroke-width="2"/>
    </svg>

    <div class="brand">
      <span class="brand-name">Pivot</span>
      <span class="brand-dot" aria-hidden="true"></span>
    </div>

    <div class="person">
      <div class="person-name">Dana Reyes</div>
      <div class="person-role">General Manager</div>
    </div>

    <div class="contact-line phone">
      <svg viewBox="0 0 16 16" aria-hidden="true"><path d="M4 1 L6.5 4 L5 6 C6 8.5 7.5 10 10 11 L12 9.5 L15 12 L13 15 C7 14.5 1.5 9 1 3 Z" fill="#e0161e"/></svg>
      <span>021 555 0147</span>
    </div>
    <div class="contact-line mobile">
      <svg viewBox="0 0 16 16" aria-hidden="true"><rect x="4" y="1" width="8" height="14" rx="1.5" fill="none" stroke="#e0161e" stroke-width="1.5"/><line x1="7" y1="12.5" x2="9" y2="12.5" stroke="#e0161e" stroke-width="1.5"/></svg>
      <span>021 555 0147</span>
    </div>
    <div class="contact-line address">
      <span>42 Harbor Lane, 5th Floor, Suite 12</span>
    </div>

    <div class="divider" aria-hidden="true"></div>

    <div class="contact-line email">
      <svg viewBox="0 0 16 16" aria-hidden="true"><rect x="1" y="3" width="14" height="10" fill="#e0161e"/><path d="M1 3 L8 9 L15 3" fill="none" stroke="#141414" stroke-width="1.2"/></svg>
      <span>dana@pivotmedia.co</span>
    </div>
    <div class="contact-line web">
      <svg viewBox="0 0 16 16" aria-hidden="true"><circle cx="8" cy="8" r="6.5" fill="none" stroke="#e0161e" stroke-width="1.4"/><ellipse cx="8" cy="8" rx="3" ry="6.5" fill="none" stroke="#e0161e" stroke-width="1.2"/><line x1="1.5" y1="8" x2="14.5" y2="8" stroke="#e0161e" stroke-width="1.2"/></svg>
      <span>www.pivotmedia.co</span>
    </div>
  </section>

  <section class="card card-back" aria-label="Business card back">
    <div class="back-brand">
      <span class="brand-name">Pivot</span>
      <span class="brand-dot" aria-hidden="true"></span>
    </div>
  </section>
</main>
</body>
</html>
```